Stylish Business Cards Wanted

- DOUBLE SIDED Design Required -

High end, edgy cards for a corporate and personal stylist. Must include logo,
Name: Belinda Harwick
Title: Director and Stylist
telephone : +61 8 7142 5809
email: belinda@theloombriefing.example
website: theloombriefing.example
Tag: Corporate Workwear & Uniform Specialist | Personal Stylist
Would like nice icons for telephone, email, website

Target Market(s)

Businesses wanting stylish uniforms, people wanting stylish wardrobes

Industry/Entity Type

Corporate Workwear Stylist

Contact Information for Business Card

I would like black, white and gold foiling incorporated in the design - possibly a touch of the other colours on my branding guide attached Name: Belinda Harwick Title: Director and Stylist telephone : +61 8 7142 5809 email: belinda@theloombriefing.example website: theloombriefing.example Tag: Corporate Workwear & Uniform Specialist | Personal Stylist Would like nice icons for telephone, email, website

Font styles to use
Other font styles liked:
• Raleway

Colors

Designer to choose colors to be used in the design.

Requirements
Must have
• Gold foil accents

```html
<!DOCTYPE html>
<html lang="en">
<head>
<meta charset="utf-8">
<title>The Loom Briefing — Business Card</title>
<link rel="stylesheet" href="https://fonts.googleapis.com/css2?family=Raleway:wght@300;400;500;600&display=swap">
<style>
  :root {
    --backdrop: #2b2b2c;
    --card-dark: #1f1f20;
    --card-light: #f3f3f5;
    --gold: #d9b45a;
    --magenta: #a0165e;
    --ink: #1a1a1a;
    --text-soft: #c9c9cb;
    --text-muted: #9a9a9c;
  }
  * { box-sizing: border-box; margin: 0; padding: 0; }
  html, body {
    width: 1200px;
    height: 868px;
    overflow: hidden;
    background: var(--backdrop);
    font-family: "Raleway", sans-serif;
  }
  .stage {
    width: 1200px;
    height: 868px;
    display: flex;
    align-items: center;
    justify-content: center;
    gap: 90px;
  }
  .card {
    width: 340px;
    height: 556px;
    border-bottom: 8px solid var(--magenta);
    box-shadow: 0 18px 40px rgba(0,0,0,0.45);
    display: flex;
    flex-direction: column;
    align-items: center;
    justify-content: center;
    text-align: center;
  }
  .card--back { background: var(--card-dark); }
  .card--front { background: var(--card-light); }

  .person-name {
    color: var(--gold);
    font-weight: 500;
    font-size: 22px;
    letter-spacing: 0.04em;
    text-transform: uppercase;
  }
  .person-title {
    color: var(--text-soft);
    font-weight: 400;
    font-size: 14px;
    margin-top: 4px;
  }
  .divider {
    width: 16px;
    height: 2px;
    background: var(--magenta);
    margin: 20px 0;
  }
  .contact-list { list-style: none; }
  .contact-item {
    display: flex;
    align-items: center;
    justify-content: center;
    gap: 7px;
    color: var(--text-soft);
    font-size: 13px;
    font-weight: 400;
    line-height: 1.6;
  }
  .contact-icon { width: 11px; height: 11px; fill: var(--gold); flex: none; }
  .services {
    list-style: none;
    color: var(--text-muted);
    font-size: 12.5px;
    font-weight: 400;
    letter-spacing: 0.06em;
    text-transform: uppercase;
    line-height: 1.5;
  }

  .brand {
    display: flex;
    align-items: center;
    gap: 12px;
  }
  .brand-mark {
    width: 14px;
    height: 14px;
    background: var(--ink);
  }
  .brand-name {
    color: var(--ink);
    font-weight: 600;
    font-size: 26px;
    letter-spacing: 0.02em;
  }
</style>
</head>
<body>
<main class="stage">
  <section class="card card--back" aria-label="Card back with contact details">
    <h1 class="person-name">Belinda Harwick</h1>
    <p class="person-title">Director &amp; Stylist</p>
    <div class="divider"></div>
    <ul class="contact-list">
      <li class="contact-item">
        <svg class="contact-icon" viewBox="0 0 24 24" aria-hidden="true"><path d="M6.6 10.8c1.4 2.8 3.8 5.1 6.6 6.6l2.2-2.2c.3-.3.7-.4 1-.2 1.1.4 2.3.6 3.6.6.6 0 1 .4 1 1V20c0 .6-.4 1-1 1C10.6 21 3 13.4 3 4c0-.6.4-1 1-1h3.5c.6 0 1 .4 1 1 0 1.3.2 2.5.6 3.6.1.3 0 .7-.2 1z"/></svg>
        +61 8 7142 5809
      </li>
      <li class="contact-item">
        <svg class="contact-icon" viewBox="0 0 24 24" aria-hidden="true"><path d="M2 5h20v14H2z M3.5 6.5 12 13l8.5-6.5" fill="var(--gold)"/><path d="M3 6l9 7 9-7" fill="none" stroke="#1f1f20" stroke-width="1.6"/></svg>
        belinda@theloombriefing.example
      </li>
      <li class="contact-item">
        <svg class="contact-icon" viewBox="0 0 24 24" aria-hidden="true"><circle cx="12" cy="12" r="10"/><path d="M2 12h20M12 2c3 3 3 17 0 20M12 2c-3 3-3 17 0 20" fill="none" stroke="#1f1f20" stroke-width="1.4"/></svg>
        theloombriefing.example
      </li>
    </ul>
    <div class="divider"></div>
    <ul class="services">
      <li>Corporate Workwear</li>
      <li>Uniform Specialist</li>
      <li>Personal Stylist</li>
    </ul>
  </section>

  <section class="card card--front" aria-label="Card front with brand name">
    <div class="brand">
      <span class="brand-mark" aria-hidden="true"></span>
      <span class="brand-name">The Loom Briefing</span>
    </div>
  </section>
</main>
</body>
</html>
```